Website for Plumbing Company, Kettleflow Plumbing Co.

I need a 7-page fully HTML-coded website for my plumbing company, Kettleflow Plumbing Co.. We specialize in installation, repair, and replacement of both gas and electric water heaters. Although we offer both tankless (on-demand) water heaters and standard (with tank) water heaters, most of our business is related to standard (with tank) water heaters in the USA market.

These are the pages I need:
1. Home page with sections such as About Us, Our Services, Why Choose Us, Testimonials, Location Map (Palm Beach County Florida), Quote Request Form, Join Our Newsletter, Mission Statement, etc.

2. Gas Water Heaters

3. Electric Water Heaters

4. Tankless Water Heaters

5. About Us

6. Contact Us

7. Privacy Policy, Terms & Conditions

Be sure to mention the following points:
1. Same-Day Service
2. Best Price Guarantee
3. 100% Satisfaction Rating
4. 15-Year Warranty on Water Heater & Parts
5. Lifetime Warranty on Workmanship
*All Warranties are Transferrable Upon Home Sale

Once design is selected and finalized, I need the website coded in a standard HTML/CSS and temporarily hosted on your development server so I can see the website functionality that is not observable from screenshots, such as section animations, etc. Once those details are finalized, I will move the source code to my server and complete the project.

Residential Home Owners and Business Owners

Plumbing, Home Services, Remodeling, Construction

0054AA
0677BA
7BADD7
CADEEF
E8F1F8
FFC000
F8CF3A
FAE287
FDF2CF
FEFAEE
EE7325
F08F49
F5BC92
FAE3D3
FDF4ED

• Clean, colorful, and professional

```html
<!DOCTYPE html>
<html lang="en">
<head>
<meta charset="utf-8">
<title>Kettleflow Plumbing Co. – Palm Beach County's Water Heater Specialists</title>
<link href="https://fonts.googleapis.com/css2?family=Poppins:wght@400;500;600;700;800&display=swap" rel="stylesheet">
<style>
:root{
  --navy:#0b1640;
  --navy-deep:#070e2b;
  --blue:#0054AA;
  --blue-2:#0677BA;
  --sky:#7BADD7;
  --orange:#EE7325;
  --yellow:#FFC000;
  --ink:#1d2233;
  --muted:#5b6275;
  --white:#ffffff;
}
*{box-sizing:border-box;margin:0;padding:0}
html,body{width:1200px;height:5384px;overflow:hidden}
body{font-family:"Poppins",sans-serif;color:var(--ink);background:var(--white)}
section,header,footer{position:relative;width:1200px;overflow:hidden}
.btn{display:inline-block;background:var(--orange);color:var(--white);font-weight:600;font-size:15px;padding:11px 26px;border-radius:24px;text-decoration:none;white-space:nowrap}
.wave{position:absolute;left:0;width:1200px}

/* header */
.site-header{height:112px}
.topbar{position:absolute;left:560px;top:0;width:640px;height:36px;background:var(--navy);border-bottom-left-radius:26px;display:flex;align-items:center;justify-content:space-around;color:var(--white);font-size:15px;font-weight:600;white-space:nowrap}
.topbar .phone{display:flex;align-items:center;gap:8px}
.brand{position:absolute;left:110px;top:28px;display:flex;align-items:center;gap:10px;white-space:nowrap}
.brand .dot{width:44px;height:44px;border-radius:50%;background:var(--blue)}
.brand .name{font-size:22px;font-weight:700;color:var(--blue)}
.nav{position:absolute;left:420px;top:60px;display:flex;gap:26px;font-size:14px;font-weight:500;white-space:nowrap}
.nav a{color:var(--ink);text-decoration:none}
.nav a.active{color:var(--blue);border-bottom:2px solid var(--orange);padding-bottom:3px}

/* hero */
.hero{height:530px}
.hero-photo{position:absolute;inset:0;background:linear-gradient(90deg,#1c2230 0%,#3d3b3a 40%,#8a8378 70%,#b7b0a6 100%)}
.hero-copy{position:absolute;left:112px;top:130px;color:var(--white)}
.hero-copy h1{font-size:44px;line-height:1.15;font-weight:700}
.hero-copy p{font-size:15px;font-weight:500;margin-top:10px;line-height:1.5}
.hero-copy .btn{margin-top:18px}

/* services */
.services{height:730px;padding-top:130px}
.sec-title{text-align:center;font-size:40px;font-weight:700;color:var(--navy)}
.sec-title span{color:var(--orange)}
.underline{width:70px;height:4px;background:var(--orange);margin:10px auto 0;border-radius:2px}
.cards{position:absolute;top:220px;left:112px;display:flex;gap:36px}
.card{width:300px;text-align:center}
.card .pic{height:250px;border-bottom:8px solid var(--blue);border-radius:0 0 50% 50%/0 0 24px 24px}
.card h3{font-size:18px;font-weight:700;margin-top:26px}
.card p{font-size:14px;color:var(--muted);margin:10px 24px 0;line-height:1.55}
.read{display:inline-block;margin-top:12px;color:var(--orange);font-weight:600;font-size:15px}
.read b{color:var(--blue)}

/* why */
.why{height:480px;background:var(--navy)}
.why .sec-title{color:var(--white);padding-top:80px}
.perks{position:absolute;top:200px;left:70px;width:1060px;display:flex;justify-content:space-between;text-align:center}
.perk{width:200px;color:var(--white);font-size:14px;font-weight:700;line-height:1.4}
.perk .ic{width:84px;height:84px;border-radius:50%;background:var(--orange);margin:0 auto 14px;position:relative;display:flex;align-items:center;justify-content:center}
.perk .ic i{position:absolute;top:-6px;right:-2px;width:24px;height:24px;border-radius:50%;background:var(--white)}

/* about & mission */
.split h2{font-size:40px;font-weight:700;color:var(--navy)}
.split h2 span{color:var(--orange)}
.split .bar{width:60px;height:4px;background:var(--orange);margin:8px 0 20px}
.split p{font-size:15px;color:var(--muted);line-height:1.65;margin-bottom:16px}
.about{height:580px}
.about .copy{position:absolute;left:112px;top:140px;width:430px}
.about .frame{position:absolute;left:660px;top:150px;width:430px;height:330px;border:4px solid var(--blue);border-radius:18px}
.about .pic{position:absolute;left:636px;top:126px;width:430px;height:330px;border-radius:18px}

/* request */
.request{height:720px;background:#0a0a0d}
.request .pic{position:absolute;left:0;top:0;width:560px;height:720px}
.form{position:absolute;left:545px;top:100px;width:555px}
.form h2{color:var(--white);font-size:32px;font-weight:600;white-space:nowrap}
.form .bar{width:60px;height:4px;background:var(--orange);margin:6px 0 24px}
.row{display:flex;gap:16px;margin-bottom:16px}
.field{flex:1;height:44px;background:var(--white);border-radius:4px;font-size:14px;color:var(--muted);padding:12px 14px;position:relative}
.field.ta{height:92px}
.field .caret{position:absolute;right:14px;top:18px;border:6px solid transparent;border-top-color:var(--ink)}

/* mission */
.mission{height:500px}
.mission .frame{position:absolute;left:112px;top:50px;width:450px;height:370px;border:4px solid var(--orange);border-radius:14px}
.mission .pic{position:absolute;left:128px;top:66px;width:430px;height:340px;border-radius:12px}
.mission .copy{position:absolute;left:630px;top:80px;width:460px}

/* testimonials */
.testimonials{height:650px;background:var(--navy)}
.testimonials .sec-title{color:var(--white);font-size:34px;padding-top:90px}
.quotes{position:absolute;top:180px;left:100px;display:flex;gap:36px}
.quote{width:310px;text-align:center}
.quote .box{background:var(--white);border-radius:10px;height:170px;padding:62px 18px 0;position:relative;font-size:13px;line-height:1.5;margin-top:46px}
.quote .avatar{position:absolute;left:115px;top:-46px;width:80px;height:80px;border-radius:50%;background:linear-gradient(#8aa0b8,#dfe6ee);border:4px solid var(--white)}
.quote .who{display:flex;justify-content:center;gap:34px;color:var(--white);font-size:14px;margin-top:16px}
.stars{color:var(--yellow);letter-spacing:2px}
.testimonials .btn{position:absolute;left:50%;top:500px;transform:translateX(-50%)}

/* locations */
.locations{height:620px}
.locations .copy{position:absolute;left:112px;top:130px;width:420px}
.locations h2{font-size:40px;font-weight:800}
.locations .bar{width:60px;height:4px;background:var(--orange);margin:6px 0 18px}
.locations p{font-size:14px;line-height:1.55;margin-bottom:18px}
.info{list-style:none}
.info li{display:flex;align-items:center;gap:14px;font-size:14px;margin-bottom:16px}
.info .ic{width:34px;height:34px;border-radius:50%;background:var(--orange);display:flex;align-items:center;justify-content:center;flex:none}
.map{position:absolute;left:580px;top:110px;width:500px;height:330px;border-radius:8px;background:linear-gradient(135deg,#e9ecef,#cfe1d3 50%,#dfe7ee);box-shadow:0 6px 18px rgba(0,0,0,.15)}

/* footer */
.site-footer{height:462px;background:var(--navy);color:var(--white)}
.f-brand{position:absolute;left:112px;top:170px;display:flex;align-items:center;gap:10px;white-space:nowrap}
.f-brand .dot{width:44px;height:44px;border-radius:50%;background:var(--orange)}
.f-brand .name{font-size:24px;font-weight:700}
.f-links{position:absolute;left:520px;top:130px}
.f-links h4,.f-news h4{font-size:18px;font-weight:600;margin-bottom:14px}
.f-links ul{list-style:none;font-size:13px;line-height:1.9}
.f-links li::before{content:"";display:inline-block;width:6px;height:6px;background:var(--white);border-radius:50%;margin-right:10px;vertical-align:middle}
.f-news{position:absolute;left:760px;top:130px;width:330px}
.f-news p{font-size:13px;line-height:1.5}
.f-news .email{border-bottom:1px solid var(--white);font-size:13px;padding:10px 0 6px;margin:10px 0 20px}
.copyright{position:absolute;left:0;bottom:0;width:1200px;height:44px;background:var(--navy-deep);text-align:center;font-size:12px;line-height:44px}
</style>
</head>
<body>

<header class="site-header">
  <div class="topbar">
    <span>Request Service or an Estimate</span>
    <span class="phone">
      <svg width="16" height="16" viewBox="0 0 24 24"><path fill="#fff" d="M6.6 10.8a15 15 0 006.6 6.6l2.2-2.2a1 1 0 011-.25 11.4 11.4 0 003.6.57 1 1 0 011 1V20a1 1 0 01-1 1A17 17 0 013 4a1 1 0 011-1h3.5a1 1 0 011 1c0 1.25.2 2.45.57 3.6a1 1 0 01-.25 1z"/></svg>
      +1 561 555 0142
    </span>
  </div>
  <div class="brand"><span class="dot"></span><span class="name">Kettleflow Plumbing Co.</span></div>
  <nav class="nav">
    <a class="active" href="#">Home</a>
    <a href="#">Gas Water Heaters</a>
    <a href="#">Electric Water Heaters</a>
    <a href="#">Tankless Water Heaters</a>
    <a href="#">About Us</a>
    <a href="#">Contact Us</a>
  </nav>
</header>

<section class="hero">
  <div class="hero-photo" role="img" aria-label="Technician standing in a showroom of water heaters"></div>
  <div class="hero-copy">
    <h1>Palm Beach County's<br>Water Heater Specialists</h1>
    <p>Fast, Affordable Installation, Repair &amp; Replacement<br>Same-Day Service • Best Price Guarantee • 100% Satisfaction Rating</p>
    <a class="btn" href="#">Get Started</a>
  </div>
  <svg class="wave" style="bottom:0" height="80" viewBox="0 0 1200 80" preserveAspectRatio="none">
    <path d="M0 40 Q300 0 600 30 T1200 20 L1200 80 L0 80Z" fill="#0054AA"/>
    <path d="M0 55 Q300 15 600 45 T1200 35 L1200 80 L0 80Z" fill="#fff"/>
  </svg>
</section>

<section class="services">
  <h2 class="sec-title">OUR <span>SERVICES</span></h2>
  <div class="underline"></div>
  <div class="cards">
    <article class="card">
      <div class="pic" role="img" aria-label="Technician servicing a gas water heater" style="background:linear-gradient(#8a6b52,#c9a27d)"></div>
      <h3>GAS WATER HEATERS</h3>
      <p>Lorem ipsum dolor sit amet, consectetur adipiscing elit, sed do dolore magna aliqua.</p>
      <span class="read">Read More <b>➜</b></span>
    </article>
    <article class="card">
      <div class="pic" role="img" aria-label="Electric water heater with expansion tank" style="background:linear-gradient(#b9b7b4,#e4e2de)"></div>
      <h3>ELECTRIC WATER HEATERS</h3>
      <p>Lorem ipsum dolor sit amet, consectetur adipiscing elit, sed do dolore magna aliqua.</p>
      <span class="read">Read More <b>➜</b></span>
    </article>
    <article class="card">
      <div class="pic" role="img" aria-label="Tankless water heater unit on a wall" style="background:linear-gradient(#9fb4c6,#dfe8ef)"></div>
      <h3>TANKLESS WATER HEATERS</h3>
      <p>Lorem ipsum dolor sit amet, consectetur adipiscing elit, sed do dolore magna aliqua.</p>
      <span class="read">Read More <b>➜</b></span>
    </article>
  </div>
</section>

<section class="why">
  <h2 class="sec-title">WHY CHOOSE US</h2>
  <div class="underline"></div>
  <div class="perks">
    <div class="perk"><div class="ic"><i></i><svg width="36" height="36" viewBox="0 0 24 24" fill="none" stroke="#fff" stroke-width="2"><circle cx="12" cy="12" r="9"/><path d="M12 7v5l3 2"/></svg></div>SAME-DAY<br>SERVICE</div>
    <div class="perk"><div class="ic"><i></i><svg width="36" height="36" viewBox="0 0 24 24" fill="none" stroke="#fff" stroke-width="2"><path d="M3 12l9-9h8v8l-9 9z"/><circle cx="16" cy="8" r="1.5"/></svg></div>BEST PRICE<br>GUARANTEE</div>
    <div class="perk"><div class="ic"><i></i><svg width="36" height="36" viewBox="0 0 24 24" fill="none" stroke="#fff" stroke-width="2"><path d="M7 11v9H3v-9zM7 11l4-8a2 2 0 012 2v4h6a2 2 0 012 2l-2 7a2 2 0 01-2 2H7"/></svg></div>100% SATISFACTION<br>RATING</div>
    <div class="perk"><div class="ic"><i></i><svg width="36" height="36" viewBox="0 0 24 24" fill="none" stroke="#fff" stroke-width="2"><path d="M12 2l8 4v6c0 5-4 9-8 10-4-1-8-5-8-10V6z"/><path d="M8 12l3 3 5-6"/></svg></div>15-YEAR WARRANTY<br>ON WATER HEATER &amp; PARTS</div>
    <div class="perk"><div class="ic"><i></i><svg width="36" height="36" viewBox="0 0 24 24" fill="none" stroke="#fff" stroke-width="2"><path d="M14 6l4 4-9 9H5v-4zM14 6l2-2 4 4-2 2"/></svg></div>LIFETIME WARRANTY<br>ON WORKMANSHIP</div>
  </div>
  <svg class="wave" style="bottom:0" height="110" viewBox="0 0 1200 110" preserveAspectRatio="none">
    <path d="M0 70 Q250 20 600 60 T1200 30 L1200 110 L0 110Z" fill="#0677BA"/>
    <path d="M0 85 Q250 35 600 75 T1200 45 L1200 110 L0 110Z" fill="#7BADD7"/>
    <path d="M0 95 Q250 50 600 88 T1200 60 L1200 110 L0 110Z" fill="#fff"/>
  </svg>
</section>

<section class="split about">
  <div class="copy">
    <h2>ABOUT <span>US</span></h2>
    <div class="bar"></div>
    <p>Lorem ipsum dolor sit amet, consectetur adipiscing elit, sed do eiusmod tempor incididunt ut labore et dolore magna aliqua.</p>
    <p>Ut enim ad minim veniam, quis nostrud exercitation ullamco laboris nisi ut aliquip ex ea commodo consequat. Duis aute irure dolor in reprehenderit in voluptate velit esse cillum dolore eu fugiat nulla pariatur.</p>
    <a class="btn" href="#">Read More</a>
  </div>
  <div class="frame"></div>
  <div class="pic" role="img" aria-label="Technician beside a service van" style="background:linear-gradient(135deg,#d7dde3,#f3f5f7 50%,#6d8fb5)"></div>
</section>

<section class="request">
  <div class="pic" role="img" aria-label="Smiling plumber giving a thumbs up next to a water heater" style="background:linear-gradient(90deg,#5b4b3d,#8d7461 55%,#0a0a0d)"></div>
  <div class="form">
    <h2>Request Service or an Estimate</h2>
    <div class="bar"></div>
    <div class="row"><div class="field">Name</div><div class="field">Email</div></div>
    <div class="row"><div class="field">City/Town</div><div class="field">Services Needed<span class="caret"></span></div></div>
    <div class="row"><div class="field ta">Comment</div></div>
    <a class="btn" href="#" style="border-radius:6px">Submit</a>
  </div>
</section>

<section class="split mission">
  <div class="frame"></div>
  <div class="pic" role="img" aria-label="Technician working on water heater pipes" style="background:linear-gradient(135deg,#6b5648,#b2855f 60%,#3d3a38)"></div>
  <div class="copy">
    <h2>OUR <span>MISSION</span></h2>
    <div class="bar"></div>
    <p>Lorem ipsum dolor sit amet, consectetur adipiscing elit, sed do eiusmod tempor incididunt ut labore et dolore magna aliqua.</p>
    <p>Ut enim ad minim veniam, quis nostrud exercitation ullamco laboris nisi ut aliquip ex ea commodo consequat. Duis aute irure dolor in reprehenderit in voluptate velit esse cillum dolore eu fugiat nulla pariatur.</p>
    <a class="btn" href="#">Read More</a>
  </div>
</section>

<section class="testimonials">
  <h2 class="sec-title">What Our <span>Customers</span> are Saying</h2>
  <div class="quotes">
    <div class="quote">
      <div class="box"><span class="avatar" role="img" aria-label="Customer portrait"></span>"I have used them twice for plumbing issues. They arrived quickly... The plumbers they sent were professional and completed the job efficiently..."</div>
      <div class="who"><span>Dana L.</span><span class="stars">★★★★★</span></div>
    </div>
    <div class="quote">
      <div class="box"><span class="avatar" role="img" aria-label="Customer portrait"></span>"They were awesome when installing our tankless water heater. We liked their professionalism so much that I'm answering all my questions."</div>
      <div class="who"><span>Marla K.</span><span class="stars">★★★★★</span></div>
    </div>
    <div class="quote">
      <div class="box"><span class="avatar" role="img" aria-label="Customer portrait"></span>"Installed a new heater for our house, did an excellent job. Their crew was very friendly and professional. Excellent installation."</div>
      <div class="who"><span>Tom-Ellis R.</span><span class="stars">★★★★★</span></div>
    </div>
  </div>
  <a class="btn" href="#">More Client Reviews</a>
  <svg class="wave" style="bottom:0" height="90" viewBox="0 0 1200 90" preserveAspectRatio="none">
    <path d="M0 50 Q300 10 600 45 T1200 25 L1200 90 L0 90Z" fill="#0677BA"/>
    <path d="M0 65 Q300 25 600 60 T1200 40 L1200 90 L0 90Z" fill="#fff"/>
  </svg>
</section>

<section class="locations">
  <div class="copy">
    <h2>LOCATIONS</h2>
    <div class="bar"></div>
    <p>We deliver training throughout FL but our primary training location is in LAKE WORTH.</p>
    <ul class="info">
      <li><span class="ic"><svg width="16" height="16" viewBox="0 0 24 24"><path fill="#fff" d="M12 2a7 7 0 00-7 7c0 5 7 13 7 13s7-8 7-13a7 7 0 00-7-7zm0 9.5A2.5 2.5 0 1112 6a2.5 2.5 0 010 5.5z"/></svg></span>24 Harbor Lane, Lake Worth FL 33460</li>
      <li><span class="ic"><svg width="16" height="16" viewBox="0 0 24 24"><path fill="#fff" d="M6.6 10.8a15 15 0 006.6 6.6l2.2-2.2a1 1 0 011-.25 11.4 11.4 0 003.6.57 1 1 0 011 1V20a1 1 0 01-1 1A17 17 0 013 4a1 1 0 011-1h3.5a1 1 0 011 1c0 1.25.2 2.45.57 3.6a1 1 0 01-.25 1z"/></svg></span>+1 561 555 0142</li>
      <li><span class="ic"><svg width="16" height="16" viewBox="0 0 24 24"><path fill="#fff" d="M3 5h18v14H3zm2 2v.4l7 4.6 7-4.6V7z"/></svg></span>info@kettleflow-demo.com</li>
      <li><span class="ic"><svg width="16" height="16" viewBox="0 0 24 24" fill="none" stroke="#fff" stroke-width="2.4"><circle cx="12" cy="12" r="8"/><path d="M12 8v4l3 2"/></svg></span>Mon – Fri 7:30am to 4:30pm</li>
    </ul>
  </div>
  <div class="map" role="img" aria-label="Street map of the Lake Worth service area"></div>
</section>

<footer class="site-footer">
  <svg class="wave" style="top:0" height="110" viewBox="0 0 1200 110" preserveAspectRatio="none">
    <path d="M0 0 H1200 V40 Q900 90 600 50 T0 60Z" fill="#fff"/>
    <path d="M0 60 Q300 30 600 50 T1200 40 L1200 52 Q900 100 600 64 T0 74Z" fill="#7BADD7"/>
    <path d="M0 74 Q300 44 600 64 T1200 52 L1200 62 Q900 110 600 76 T0 86Z" fill="#0677BA"/>
  </svg>
  <div class="f-brand"><span class="dot"></span><span class="name">Kettleflow Plumbing Co.</span></div>
  <div class="f-links">
    <h4>Other Links</h4>
    <ul><li>FAQ</li><li>Terms of Use</li><li>Privacy Policy</li><li>Support Links</li><li>Conditions</li></ul>
  </div>
  <div class="f-news">
    <h4>Sign Up to Our Newsletter</h4>
    <p>Lorem ipsum dolor sit amet, consectetur adipiscing elit, adipiscing elit.</p>
    <div class="email">Email</div>
    <a class="btn" href="#">Subscribe</a>
  </div>
  <div class="copyright">COPYRIGHT@2025 COMPANY NAME. ALL RIGHTS RESERVED</div>
</footer>

</body>
</html>
```